Exciting & Elegant Stationary Pack

Stationary consists of
1. Letter head / Envelope
2. Business Card
3. Invoice
4. 40x40mm sticker

Attached files;

1. Logo (Other formats available on request)
2. MS word Doc - For information and description of design
3. Website image (This will be our new website so use the colours so everything ties together)
4. Sample of stationary pack we like, but feel free to be creative

Target Market(s)

Home improvement

Industry/Entity Type

Construction

Font styles to use
Other font styles liked:
• Leave up to designer - We like font used on (website attached image)

Requirements
Must have
• Please look at uploaded file of sample website and use colours
Nice to have
• Any type of business card design - eg. metal, die cut, embossed, etc...

```html
<!DOCTYPE html>
<html lang="en">
<head>
<meta charset="utf-8">
<title>Ashgrove Tiling – Business Card</title>
<link rel="stylesheet" href="https://fonts.googleapis.com/css2?family=Open+Sans:wght@400;600;700&display=swap">
<style>
  :root {
    --page-bg: #d9d4cd;
    --card-bg: #eef0f1;
    --navy: #1b2c44;
    --navy-deep: #14233a;
    --orange: #e06a26;
    --orange-dark: #c9561a;
    --title-tint: #fbdac6;
    --contact-text: #e3e8ee;
    --icon: #ea7434;
  }
  * { margin: 0; padding: 0; box-sizing: border-box; }
  html, body {
    width: 1200px; height: 969px; overflow: hidden;
    background: var(--page-bg);
    font-family: "Open Sans", Arial, sans-serif;
  }
  .card {
    position: absolute; left: 100px; top: 200px;
    width: 1000px; height: 569px;
    background: var(--card-bg);
    overflow: hidden;
    box-shadow: 0 12px 40px rgba(0,0,0,.18);
  }
  .card-shapes { position: absolute; inset: 0; }
  .brand-name {
    position: absolute; left: 500px; width: 470px; top: 104px;
    text-align: center; white-space: nowrap;
    font-size: 40px; font-weight: 700; letter-spacing: 2px;
    color: var(--navy); line-height: 1;
  }
  .holder { position: absolute; left: 60px; top: 278px; }
  .holder-name {
    font-size: 32px; font-weight: 700; color: #fff; letter-spacing: .5px; line-height: 1.1;
  }
  .holder-role {
    font-size: 25px; font-weight: 400; color: var(--title-tint); letter-spacing: .5px; margin-top: 4px;
  }
  .contacts { position: absolute; left: 62px; top: 420px; list-style: none; }
  .contact {
    display: flex; align-items: center; height: 38px;
    font-size: 26px; color: var(--contact-text);
  }
  .contact svg { width: 24px; height: 24px; margin-right: 14px; flex: none; }
  .licence {
    position: absolute; right: 35px; top: 495px;
    font-size: 26px; color: var(--contact-text);
  }
</style>
</head>
<body>
  <div class="card">
    <svg class="card-shapes" width="1000" height="569" viewBox="0 0 1000 569">
      <defs>
        <linearGradient id="navyBand" x1="0" y1="0" x2="0" y2="1">
          <stop offset="0" stop-color="#22354f"/>
          <stop offset="1" stop-color="#14233a"/>
        </linearGradient>
        <linearGradient id="orangeBand" x1="0" y1="0" x2="0" y2="1">
          <stop offset="0" stop-color="#e8762f"/>
          <stop offset="1" stop-color="#d4601f"/>
        </linearGradient>
      </defs>
      <polygon class="diagonal-band" points="539,170 940,170 967,200 967,362 707,362" fill="url(#navyBand)"/>
      <polygon class="name-band" points="0,264 595,264 707,362 0,362" fill="url(#orangeBand)"/>
      <rect class="contact-band" x="0" y="362" width="1000" height="207" fill="url(#navyBand)"/>
    </svg>

    <div class="brand-name">ASHGROVE TILING</div>

    <div class="holder">
      <div class="holder-name">LINH TRAN</div>
      <div class="holder-role">PROJECT MANAGER</div>
    </div>

    <ul class="contacts">
      <li class="contact">
        <svg viewBox="0 0 24 24"><rect x="6" y="1.5" width="12" height="21" rx="2" fill="none" stroke="var(--icon)" stroke-width="2.2"/><circle cx="12" cy="18.5" r="1.3" fill="var(--icon)"/></svg>
        0400 555 128
      </li>
      <li class="contact">
        <svg viewBox="0 0 24 24"><rect x="2" y="5" width="20" height="14" fill="var(--icon)"/><path d="M2 5 L12 13 L22 5" fill="none" stroke="var(--navy)" stroke-width="1.8"/></svg>
        hello@ashgrovetiling.com.au
      </li>
      <li class="contact">
        <svg viewBox="0 0 24 24"><circle cx="12" cy="12" r="10" fill="var(--icon)"/><ellipse cx="12" cy="12" rx="4.5" ry="10" fill="none" stroke="var(--navy)" stroke-width="1.5"/><path d="M2 12 H22" stroke="var(--navy)" stroke-width="1.5"/></svg>
        www.ashgrovetiling.com.au
      </li>
    </ul>

    <div class="licence">Lic No.,204516c</div>
  </div>
</body>
</html>
```